Launch Website

A very simple, but attractive website (template preferred) is required in a common format - HTML5 or Wordpress etc.
It should be easily user updateable for updates.
Pages it needs:
-Home Page with menu bar, company logo and 1 large graphic/picture and two smaller graphics/logos.
- What we do
- How we do it
- About Us
- Guarantees
- Results
- Contact Page with Enquiry Form
- Provision for a blog to be added later

Most pages will be approx 150 words text with some small/medium images.
We have our own domain & hosting.

A "less is more" design approach would be encouraged.

Target Market(s)

Vehicle Fleet Managers

Industry/Entity Type

It Company

Font styles to use
Sans Serif

Colors
9bcb3c

Requirements
Must have
• Corporate Style. No Fluff.
Nice to have
• Images of LIght Commerical vehicles and trucks

Am ok with white background throughout site.
Colours should match/complement company logo.
Should not have
• Should not be too "busy"

```html
<!DOCTYPE html>
<html lang="en">
<head>
<meta charset="utf-8">
<title>Clearline Fleet</title>
<link rel="stylesheet" href="https://fonts.googleapis.com/css2?family=Roboto+Condensed:wght@400;700&family=Open+Sans:wght@400;600&display=swap">
<style>
:root{
  --brand-green:#17a04a;
  --brand-blue:#1a93d4;
  --navy:#134a80;
  --navy-light:#1d5c98;
  --ink:#222;
  --muted:#8a8a8a;
  --text:#7b7b7b;
  --red:#d6222a;
  --rule:#d9d9d9;
  --btn:#c9c9c9;
  --footer:#eeeeee;
  --white:#fff;
}
*{margin:0;padding:0;box-sizing:border-box}
html,body{width:1200px;height:1003px;overflow:hidden;background:var(--white)}
body{position:relative;font-family:"Open Sans",Arial,sans-serif;color:var(--text)}
.site-header{position:absolute;left:0;top:0;width:1200px;height:102px;background:linear-gradient(#ffffff,#f1f1f1)}
.brand{position:absolute;left:131px;top:30px;display:flex;align-items:center;gap:10px}
.brand-mark{width:14px;height:14px;background:var(--brand-green)}
.brand-name{font-family:"Open Sans",Arial,sans-serif;font-weight:600;font-size:32px;line-height:40px;color:var(--brand-green)}
.contact{position:absolute;right:132px;top:24px;text-align:right;font-size:14.5px;color:var(--muted);line-height:20px}
.contact .phone{color:var(--red);font-size:21px}
.contact .email{color:var(--ink)}
.contact-icon{position:absolute;left:808px;top:26px}
.hero-band{position:absolute;left:0;top:102px;width:1200px;height:442px;background:linear-gradient(var(--navy),var(--navy-light) 60%,var(--navy))}
.main-nav{position:absolute;left:0;top:102px;width:1200px;height:46px}
.main-nav a{font-family:"Roboto Condensed",Arial,sans-serif;font-size:15px;color:var(--white);text-decoration:none;position:absolute;top:14px}
.slider{position:absolute;left:131px;top:155px;width:938px;height:469px;background:var(--white);border-radius:3px}
.slider-shadow{position:absolute;left:150px;top:618px;width:900px;height:22px;border-radius:50%;background:radial-gradient(ellipse at center,rgba(0,0,0,.25),rgba(0,0,0,0) 70%)}
.slide-photo{position:absolute;left:9px;top:9px;width:920px;height:449px;background:linear-gradient(180deg,#7fa7cf 0%,#b9cde0 28%,#a89a78 55%,#8a7656 80%,#6b5a43 100%)}
.callout{position:absolute;left:545px;top:63px;width:362px;height:176px}
.callout-text{position:absolute;right:28px;top:20px;width:300px;font-family:"Roboto Condensed",Arial,sans-serif;color:var(--white);font-size:24px;line-height:28px}
.callout-text .line-1{text-align:right}
.callout-text .accent{display:block;padding-left:30px;color:var(--brand-blue);font-size:20px}
.callout-text .big{display:block;padding-left:28px;color:var(--brand-blue);font-weight:700;font-size:30px;line-height:44px}
.callout-text .big b{font-size:50px}
.callout-text .line-4{display:block;text-align:right}
.badge{position:absolute;top:356px;height:74px;background:var(--white)}
.badge-member{left:547px;width:127px}
.badge-member span{position:absolute;left:14px;top:12px;width:99px;height:50px;background:#cfd3d8}
.badge-partner{left:685px;width:223px;display:flex;align-items:center;justify-content:center}
.badge-partner span{font-family:"Open Sans",Arial,sans-serif;font-size:24px;color:var(--brand-blue)}
.dots{position:absolute;left:29px;top:426px;display:flex;gap:2px}
.dots i{display:block;width:9px;height:9px;background:var(--white)}
.dots i:first-child{background:var(--brand-blue)}
.features{position:absolute;left:131px;top:681px;display:flex;gap:37px}
.feature{width:206px}
.feature h2{font-family:"Roboto Condensed",Arial,sans-serif;font-weight:400;font-size:21px;color:var(--brand-blue);padding-bottom:7px;border-bottom:1px solid var(--rule);position:relative}
.feature h2::after{content:"";position:absolute;left:0;bottom:-2px;width:78px;height:3px;background:var(--brand-blue)}
.feature p{margin-top:15px;font-size:12.4px;line-height:18.7px;height:96px}
.feature .more{display:inline-block;margin-top:8px;width:77px;height:24px;line-height:24px;text-align:center;background:var(--btn);color:var(--white);font-size:11.5px;border-radius:2px;text-decoration:none}
.site-footer{position:absolute;left:0;top:923px;width:1200px;height:80px;background:var(--footer)}
.legal{position:absolute;left:131px;top:21px;font-size:13px;line-height:19px;color:var(--muted)}
.social{position:absolute;left:960px;top:25px;display:flex;gap:9px}
.social a{display:block;width:30px;height:30px;background:#1f6db5}
</style>
</head>
<body>
<header class="site-header">
  <div class="brand">
    <span class="brand-mark" aria-hidden="true"></span>
    <div class="brand-name">Clearline Fleet</div>
  </div>
  <svg class="contact-icon" width="52" height="56" viewBox="0 0 52 56" aria-hidden="true">
    <path d="M14 4c-6 2-8 10-6 22s8 22 16 24c4 1 6-2 5-4l-5-7c-1-2-3-2-4-1l-3 2c-3-4-5-11-5-17l4-1c1 0 2-2 1-3L15 5c0-1-1-1-1-1z" fill="#222"/>
    <path d="M20 50c8 6 20 4 28-2" stroke="#222" stroke-width="1.5" fill="none"/>
  </svg>
  <div class="contact">
    Contact us on <span class="phone">(02)5550 1234</span><br>
    or email us <span class="email">hello@clearlinefleet.com</span>
  </div>
</header>

<div class="hero-band"></div>
<nav class="main-nav">
  <a href="#" style="left:168px">HOME</a>
  <a href="#" style="left:256px">WHAT WE DO</a>
  <a href="#" style="left:390px">HOW WE DO IT</a>
  <a href="#" style="left:531px">ABOUT US</a>
  <a href="#" style="left:643px">GUARANTEES</a>
  <a href="#" style="left:778px">RESULTS</a>
  <a href="#" style="left:882px">CONTACT</a>
  <a href="#" style="left:991px">BLOG</a>
</nav>

<div class="slider-shadow"></div>
<section class="slider">
  <div class="slide-photo" role="img" aria-label="Blue diesel dump truck on a dirt road with mountains under a clear sky"></div>
  <div class="callout">
    <svg width="362" height="176" viewBox="0 0 362 176" aria-hidden="true">
      <polygon points="0,0 362,0 362,176 40,176" fill="var(--brand-blue)"/>
      <polygon points="6,0 362,0 362,170 44,170" fill="#050505"/>
    </svg>
    <div class="callout-text">
      <div class="line-1">We help diesel vehicle fleets</div>
      <span class="accent">save up to</span>
      <span class="big"><b>20%</b> FUEL COSTS</span>
      <span class="line-4">by optimising their engines.</span>
    </div>
  </div>
  <div class="badge badge-member"><span role="img" aria-label="Industry association membership badge"></span></div>
  <div class="badge badge-partner"><span>Apex Tune</span></div>
  <div class="dots"><i></i><i></i><i></i></div>
</section>

<main class="features">
  <article class="feature">
    <h2>ABOUT US</h2>
    <p>Clearline Fleet have combined over 50 years experience in all aspects of the automotive industry including commercial fleet and diesel engines. We are the ...</p>
    <a class="more" href="#">Read More</a>
  </article>
  <article class="feature">
    <h2>WHAT WE DO</h2>
    <p>Clearline Fleet delivers award winning, ISO 9001 certified diesel engine ECU remapping for fleet operations. As Principal Australian Fleet Agent for Apex Tune...</p>
    <a class="more" href="#">Read More</a>
  </article>
  <article class="feature">
    <h2>HOW WE DO IT</h2>
    <p>Clearline Fleet will conduct an obligation Free Consultation with your Fleet Representatives to determine your Fleets needs, and identify any customization...</p>
    <a class="more" href="#">Read More</a>
  </article>
  <article class="feature">
    <h2>WHY</h2>
    <p>We've acted on customer requests for cost effective, financially attractive solutions to reduce fuel and operating costs whilst also reducing environmental foot...</p>
    <a class="more" href="#">Read More</a>
  </article>
</main>

<footer class="site-footer">
  <div class="legal">Copyright 2014 Apex Tune. All Rights Reserved.<br>Privacy Policy &nbsp;|&nbsp; Terms and Conditions</div>
  <div class="social">
    <a href="#" aria-label="Social profile one"></a>
    <a href="#" aria-label="Social profile two"></a>
    <a href="#" aria-label="Social profile three"></a>
  </div>
</footer>
</body>
</html>
```